Request for Business Card Design

Hi. My name is Marlene, I am looking for a new business card design for my company, Quarrow Signal Instruments, LLC. I really like the design you did for Tarsel Venture and was hoping you could do something similar using our full logo and our mark. I am also open to any raised texture design using our mark. I have attached our full logo, which would need to be somewhere on the card, as well as the mark in both outline and full form, as well as our brand colors / guide. The card does not have to be white, as long as our logo and mark appear. I actually like darker colored business cards more, but am open to all options. If you are interested in working with me, please let me know. We would also take the business card design into letterhead design if you can do that.

```html
<!DOCTYPE html>
<html lang="en">
<head>
<meta charset="utf-8">
<title>Quarrow Signal Instruments – Business Card</title>
<link href="https://fonts.googleapis.com/css2?family=Open+Sans:wght@400;600;700&display=swap" rel="stylesheet">
<style>
  :root {
    --stage: #2a2a2d;
    --card-dark: #1e1e21;
    --card-dark-deep: #141416;
    --brand-blue: #1a9cc9;
    --brand-blue-light: #5fc3e2;
    --brand-blue-deep: #0f7fa8;
    --ink-light: #f2f2f2;
    --ink-muted: #6d6d72;
    --ink-dark: #1d2a33;
  }
  * { box-sizing: border-box; margin: 0; padding: 0; }
  html, body { width: 1200px; height: 780px; overflow: hidden; }
  body {
    background: var(--stage);
    font-family: "Open Sans", Arial, sans-serif;
    position: relative;
  }
  .card {
    position: absolute;
    top: 230px;
    width: 530px;
    height: 310px;
    border-radius: 4px;
    overflow: hidden;
    box-shadow: 0 14px 30px rgba(0,0,0,.45);
  }

  /* Front */
  .card-front { left: 40px; background: var(--card-dark); }
  .brand {
    position: absolute; left: 30px; top: 28px;
    display: flex; align-items: center; gap: 12px;
  }
  .brand-dot {
    width: 38px; height: 38px; border-radius: 50%;
    background: var(--brand-blue);
  }
  .brand-name {
    font-weight: 700; font-size: 30px; letter-spacing: 4px;
    color: var(--ink-muted); line-height: 1;
  }
  .brand-tagline {
    font-weight: 700; font-size: 8px; letter-spacing: 1.4px;
    color: var(--ink-muted); margin-top: 4px;
  }
  .contact {
    position: absolute; left: 30px; top: 118px;
    color: var(--ink-light); font-size: 13px; line-height: 1.45;
  }
  .contact-address { margin-bottom: 8px; }
  .contact-list { list-style: none; }
  .contact-list li { display: flex; align-items: center; gap: 9px; }
  .contact-list svg { width: 12px; height: 12px; fill: var(--brand-blue); flex: none; }
  .emboss-area {
    position: absolute; right: 60px; bottom: -40px;
    width: 250px; height: 250px; border-radius: 50%;
    background: radial-gradient(circle at 65% 35%, #3a3a3e 0%, #1a1a1c 55%, var(--card-dark-deep) 100%);
  }
  .holder {
    position: absolute; right: 48px; top: 150px; text-align: right;
  }
  .holder-name {
    font-weight: 700; font-size: 34px; color: var(--brand-blue); line-height: 1;
  }
  .holder-role { font-size: 15px; color: var(--ink-light); margin-top: 4px; }
  .accent-bar {
    position: absolute; right: 0; top: 150px;
    width: 18px; height: 62px; background: var(--brand-blue);
  }

  /* Back */
  .card-back {
    left: 630px;
    background: linear-gradient(100deg, var(--brand-blue-deep) 0%, var(--brand-blue) 50%, var(--brand-blue-light) 100%);
  }
  .pattern-area { position: absolute; inset: 0; }
  .brand-back {
    position: absolute; left: 50%; bottom: 40px; transform: translateX(-50%);
    display: flex; align-items: center; gap: 10px;
  }
  .brand-back .brand-dot { width: 24px; height: 24px; background: #ffffff; }
  .brand-back .brand-name { font-size: 18px; letter-spacing: 2.5px; color: var(--ink-dark); }
  .brand-back .brand-tagline { font-size: 5.5px; letter-spacing: 1px; color: var(--ink-dark); margin-top: 2px; }
</style>
</head>
<body>
  <section class="card card-front">
    <div class="brand">
      <span class="brand-dot"></span>
      <div>
        <div class="brand-name">QUARROW</div>
        <div class="brand-tagline">SIGNAL INSTRUMENTS</div>
      </div>
    </div>

    <div class="contact">
      <p class="contact-address">1180 Ridgeline Park Drive<br>Fallbrook, CO 80411</p>
      <ul class="contact-list">
        <li><svg viewBox="0 0 12 12"><path d="M2 1h2.5l1 3-1.5 1a7 7 0 0 0 3 3l1-1.5 3 1V11h-1A9 9 0 0 1 1 2V1z"/></svg>+001 303 555 0142</li>
        <li><svg viewBox="0 0 12 12"><rect x="3" y="1" width="6" height="3"/><rect x="1" y="4" width="10" height="5" rx="1"/><rect x="3" y="8" width="6" height="3"/></svg>+001 303 555 0187</li>
        <li><svg viewBox="0 0 12 12"><circle cx="6" cy="6" r="5"/></svg>www.quarrowsignal.com</li>
        <li><svg viewBox="0 0 12 12"><path d="M1 3h10v7H1z M1 3l5 4 5-4" /></svg>info@quarrowsignal.com</li>
      </ul>
    </div>

    <div class="emboss-area" role="img" aria-label="Large raised-texture brand mark decoration"></div>

    <div class="holder">
      <div class="holder-name">Marlene</div>
      <div class="holder-role">Director</div>
    </div>
    <span class="accent-bar"></span>
  </section>

  <section class="card card-back">
    <div class="pattern-area" role="img" aria-label="Repeating brand mark pattern fading from blue to light blue"></div>
    <div class="brand brand-back">
      <span class="brand-dot"></span>
      <div>
        <div class="brand-name">QUARROW</div>
        <div class="brand-tagline">SIGNAL INSTRUMENTS</div>
      </div>
    </div>
  </section>
</body>
</html>
```